Medical centre needs a business card

We are a medcial centre in Australia, needing a new business card. Our demographic is low working class families. We are going to be renovating our premises to modernise the look and also had a new logo done a few months ago representing quality and community, and now need to update our cards. It needs to be doubled sided, with logo and contact details on the front, and appointment details on the back. . Needs to be modern and simple, easy to read. <br/><br/>Name: Kindle Grove Medical Centre <br/>Address: 512 Parmley Rd (Cnr Parmley Rd & Osgood Creek Rd),<br/>Tindarra Court Shopping Centre, Paralowie, SA 5108<br/>Ph: 08 8461 3072<br/>Tag line: Where your wellbeing comes first<br/>Website: www.kindlegrovemedicalcentre-example.com.au<br/>Online bookings also available<br/><br/>(On the back, to have 3 lines of appointments that can be written in.<br/>Day, date, time)<br/><br/>Your next appointment is on<br/>Can try “M T W Th F Sa Su _________________ at ____________ am/pm” or other combinations <br/>Please advise as soon as possible if unable to attend<br/>Cancellation fees apply if less than 2 hrs notice<br/>Online appointments available (please highlight this option by either by position, colour or font)

Target Market(s)

Lower social economic working class, young families to seniors

Industry/Entity Type

Medical Centre

Contact Information for Business Card

Kindle Grove Medical Centre
512 Parmley Rd (Cnr Parmley Rd & Osgood Creek Drive)
Tindarra Court Shopping Centre
Marlowe Park SA 5199
Ph: 08 8461 3072
www.kindlegrovemedicalcentre-example.com.au
Tagline line: where your wellbeing comes first
Back side is for appointments
Your next appointment is with Dr ______________
Day/date/time (Please give 3 lines of appointments)
Please advise as soon as possible if unable to attend
Cancellation fees apply if less than 2 hours notice
Online appointments available
Book online easily and conveniently (please highlight online appointments)

Font styles to use
Serif
Sans Serif

Colors

Designer to choose colors to be used in the design.

Requirements
Must have
• Modern and simple
• Easy to ready
• Induces a wellbeing feeling
• Incorporate our logo colours and feel from logo
• Induces feeling of stability and security
Nice to have
• Attract attention
• Pleasant to look at
• Feeling of innovation
Should not have
• Loud clashing colours
• Overly luxurious feeling
• Overly artistic

```html
<!DOCTYPE html>
<html lang="en">
<head>
<meta charset="utf-8">
<title>Kindle Grove Medical Centre – Business Card</title>
<link rel="stylesheet" href="https://fonts.googleapis.com/css2?family=Open+Sans:wght@400;600;700&display=swap">
<style>
  :root {
    --blue: #0a72b9;
    --green: #9ccb3b;
    --ink: #2a2a2a;
    --rule: #777777;
    --paper: #ffffff;
    --backdrop: #262626;
  }
  * { box-sizing: border-box; margin: 0; padding: 0; }
  html, body { width: 1200px; height: 1021px; overflow: hidden; }
  body {
    background: var(--backdrop);
    font-family: "Open Sans", Arial, sans-serif;
    position: relative;
  }
  .card {
    position: absolute;
    left: 280px;
    width: 640px;
    height: 390px;
    border-radius: 2px;
    overflow: hidden;
  }

  /* Back: appointment side */
  .card-back { top: 80px; background: var(--blue); }
  .appt-panel {
    position: absolute;
    left: 38px; right: 38px; top: 32px;
    height: 232px;
    background: var(--paper);
    border-radius: 14px;
    padding: 30px 26px 0 26px;
    color: var(--ink);
    font-size: 14px;
  }
  .appt-tab {
    position: absolute;
    top: 18px; left: 250px;
    width: 290px; height: 32px;
    background: var(--green);
    color: var(--paper);
    font-weight: 600;
    font-size: 16px;
    letter-spacing: .04em;
    text-align: center;
    line-height: 32px;
    z-index: 2;
  }
  .field { display: flex; align-items: flex-end; gap: 6px; }
  .rule { flex: 1; border-bottom: 1px solid var(--rule); height: 14px; }
  .rule.short { flex: 0 0 118px; }
  .days { display: flex; justify-content: space-between; margin: 14px 0 12px; }
  .day { display: flex; align-items: center; gap: 6px; }
  .box { width: 17px; height: 14px; border: 1.5px solid var(--green); }
  .appt-row { margin-bottom: 14px; }
  .appt-row .label-time { margin-left: 10px; }
  .appt-notes {
    position: absolute;
    left: 0; right: 0; top: 276px;
    text-align: center;
    color: var(--paper);
    font-size: 14.5px;
    line-height: 1.45;
  }
  .appt-notes .online { color: var(--green); font-weight: 600; }

  /* Front: contact side */
  .card-front { top: 530px; background: var(--paper); }
  .brand {
    position: absolute; left: 48px; top: 78px;
    display: flex; align-items: center; gap: 12px;
    color: var(--blue); font-weight: 700;
  }
  .brand-mark { width: 22px; height: 22px; background: var(--blue); }
  .brand-name { font-size: 25px; line-height: 1.1; letter-spacing: .02em; }
  .brand-name small { display: block; font-size: 14px; letter-spacing: .18em; }
  .tagline {
    position: absolute; left: 48px; top: 220px; width: 230px;
    color: var(--green); font-weight: 600; font-size: 17px;
    text-transform: uppercase; text-align: center; line-height: 1.3;
  }
  .divider-blue {
    position: absolute; left: 340px; top: 72px;
    width: 2px; height: 48px; background: var(--blue);
  }
  .divider-green {
    position: absolute; left: 322px; top: 142px;
    width: 2px; height: 175px; background: var(--green);
  }
  .person { position: absolute; left: 360px; top: 70px; }
  .person-name { color: var(--blue); font-weight: 700; font-size: 22px; }
  .person-role { color: var(--ink); font-size: 16px; }
  .contact {
    position: absolute; left: 342px; top: 152px;
    color: var(--ink); font-size: 15px; line-height: 1.35;
    font-style: normal;
  }
  .contact .clinic { color: var(--blue); font-size: 16px; }
  .contact .phone { display: flex; align-items: center; gap: 6px; margin-top: 6px; font-size: 16px; }
  .site-band {
    position: absolute; left: 0; right: 0; bottom: 0; height: 48px;
    background: var(--blue);
    color: var(--paper); font-size: 17px;
    text-align: center; line-height: 48px;
  }
</style>
</head>
<body>

<section class="card card-back" aria-label="Appointment side">
  <div class="appt-tab">YOUR NEXT APPOINTMENT</div>
  <div class="appt-panel">
    <div class="field"><span>Dr.:</span><span class="rule"></span></div>
    <div class="days">
      <span class="day"><span class="box"></span>Mon</span>
      <span class="day"><span class="box"></span>Tue</span>
      <span class="day"><span class="box"></span>Wed</span>
      <span class="day"><span class="box"></span>Thu</span>
      <span class="day"><span class="box"></span>Fri</span>
      <span class="day"><span class="box"></span>Sat</span>
      <span class="day"><span class="box"></span>Sun</span>
    </div>
    <div class="field appt-row"><span>Date:</span><span class="rule"></span><span class="label-time">Time:</span><span class="rule short"></span><span>am/pm</span></div>
    <div class="field appt-row"><span>Date:</span><span class="rule"></span><span class="label-time">Time:</span><span class="rule short"></span><span>am/pm</span></div>
    <div class="field appt-row"><span>Date:</span><span class="rule"></span><span class="label-time">Time:</span><span class="rule short"></span><span>am/pm</span></div>
  </div>
  <div class="appt-notes">
    <p>Please advise as soon as possible if unable to attend</p>
    <p>Cancellation fees apply if less than 2 hours notice</p>
    <p><span class="online">Online appointments available</span> | Book online easily and conveniently</p>
  </div>
</section>

<section class="card card-front" aria-label="Contact side">
  <div class="brand">
    <span class="brand-mark"></span>
    <span class="brand-name">KINDLE GROVE<small>MEDICAL CENTRE</small></span>
  </div>
  <p class="tagline">Where your wellbeing comes first</p>

  <span class="divider-blue"></span>
  <span class="divider-green"></span>

  <div class="person">
    <p class="person-name">Daniel Harper</p>
    <p class="person-role">Founder</p>
  </div>

  <address class="contact">
    <p class="clinic">Kindle Grove Medical Centre</p>
    <p>512 Parmley Rd</p>
    <p>(Cnr Parmley Rd &amp; Osgood Creek Drive)</p>
    <p>Tindarra Court Shopping Centre</p>
    <p>Marlowe Park SA 5199</p>
    <p class="phone">
      <svg width="14" height="14" viewBox="0 0 24 24" aria-hidden="true"><path fill="#9ccb3b" d="M6.6 10.8a15.1 15.1 0 0 0 6.6 6.6l2.2-2.2a1 1 0 0 1 1-.25 11.4 11.4 0 0 0 3.6.57 1 1 0 0 1 1 1V20a1 1 0 0 1-1 1A17 17 0 0 1 3 4a1 1 0 0 1 1-1h3.5a1 1 0 0 1 1 1c0 1.25.2 2.45.57 3.57a1 1 0 0 1-.25 1z"/></svg>
      08 8461 3072
    </p>
  </address>

  <div class="site-band">www.kindlegrovemedicalcentre-example.com.au</div>
</section>

</body>
</html>
```